FinTech company looking to revamp and expand client-facing interface for our financial models

Pellworth Engines currently has a very simple website that allows clients to interact with our financial models. We are looking to completely redesign the current site and add several extra pages to provide extra functionality. We want the design to have a modern, slick feel, that will work on both a desktop or a tablet. It should be straightforward for clients to move between different pages at any time, and clear from the layout how to interact with the more advanced features. We have included screenshots of existing pages in the attached design brief, as well as sketches of the functionality required by the new pages, but can't provide a direct link to the current site.
Target Market(s)
Professional investors that will be paying to access the interface
Industry/Entity Type
Finance
Number of Pages Required
4 page
Colors
Designer to choose colors to be used in the design.
Look and feel
Each slider illustrates characteristics of the customer's brand and the style your logo design should communicate.

```html
<!DOCTYPE html>
<html lang="en">
<head>
<meta charset="utf-8">
<title>Kestrel – Sensitivities</title>
<link rel="stylesheet" href="https://fonts.googleapis.com/css2?family=Montserrat:wght@500;600;700;800&family=Roboto+Condensed:wght@400;500&display=swap">
<style>
:root{
  --page:#e6e6e6;
  --white:#ffffff;
  --ink:#111111;
  --navy:#02326a;
  --teal:#006b67;
  --black:#161616;
  --line:#e2e2e2;
  --row-alt:#f0f0f0;
  --tab:#ffffff;
  --muted:#444444;
}
*{box-sizing:border-box;margin:0;padding:0}
html,body{width:1200px;height:706px;overflow:hidden;background:var(--page)}
.stage{width:1300px;height:765px;transform:scale(.9231,.9229);transform-origin:0 0;position:relative;background:var(--page);font-family:"Montserrat",sans-serif;color:var(--ink)}
.app{position:absolute;left:15px;top:15px;width:1270px;height:735px;background:linear-gradient(#ededed 0,#e9e9e9 155px,#dcdcdc 155px,#f4f4f4 420px,#fafafa 735px);overflow:hidden}
.topbar{position:absolute;left:0;top:0;width:1270px;height:60px;background:var(--white);box-shadow:0 4px 10px rgba(0,0,0,.08);display:flex;align-items:stretch}
.brand{width:180px;padding-left:58px;display:flex;align-items:center;font-weight:800;font-size:18px}
.periods{display:flex}
.period{width:90px;display:flex;align-items:center;justify-content:center;font-weight:700;font-size:14px;border-right:1px solid var(--line)}
.period.active{background:var(--navy);color:var(--white);border-right:none}
.mainnav{position:absolute;left:585px;top:0;height:60px;display:flex}
.navitem{display:flex;align-items:center;justify-content:center;gap:8px;font-weight:700;font-size:13px;border-left:1px solid var(--line)}
.navitem svg{width:24px;height:24px}
.navitem.active{background:var(--navy);color:var(--white)}
.navitem:last-child{border-right:1px solid var(--line)}
.subtabs{position:absolute;left:0;top:0}
.subtab{position:absolute;background:var(--tab);border-radius:5px 5px 0 0;display:flex;align-items:center;justify-content:center;font-weight:600;font-size:13px;color:#333;box-shadow:0 -1px 3px rgba(0,0,0,.05)}
.subtab.active{background:var(--black);color:var(--white);font-weight:700}
.subtab.add{background:var(--navy)}
.export{position:absolute;left:1150px;top:197px;display:flex;align-items:center;gap:8px;color:var(--navy);font-weight:700;font-size:17px}
.filters{position:absolute;left:0;top:320px;width:50px;height:250px;background:var(--black);border-radius:0 6px 6px 0}
.filters span{position:absolute;left:25px;top:125px;transform:translate(-50%,-50%) rotate(-90deg);color:var(--white);font-weight:700;font-size:15px;letter-spacing:1px}
.filters-toggle{position:absolute;left:36px;top:431px;width:28px;height:28px;border-radius:50%;background:var(--white);display:flex;align-items:center;justify-content:center}
.data{position:absolute;left:90px;top:235px;width:1160px;border-collapse:collapse;border-radius:8px;overflow:hidden;box-shadow:0 3px 10px rgba(0,0,0,.12);background:var(--white)}
.data th{height:70px;font-weight:600;font-size:16px;color:var(--white);background:var(--black);border-right:1px solid #3a3a3a}
.data th.stat{background:var(--teal);border-right:1px solid #0d7d78;width:90px}
.data th.factor{width:150px}.data th.id{width:100px}.data th.sector{width:190px}
.data td{height:69px;text-align:center;font-family:"Roboto Condensed",sans-serif;font-size:17px;color:var(--ink);border-right:1px solid var(--line)}
.data tr:nth-child(even) td{background:var(--row-alt)}
.data td:last-child,.data th:last-child{border-right:none}
</style>
</head>
<body>
<div class="stage">
 <div class="app">
  <nav class="subtabs">
   <div class="subtab" style="left:55px;top:120px;width:155px;height:35px">EQUITIES</div>
   <div class="subtab" style="left:215px;top:120px;width:155px;height:35px">ETFS</div>
   <div class="subtab" style="left:375px;top:110px;width:155px;height:45px">PAIRS</div>
   <div class="subtab active" style="left:535px;top:100px;width:155px;height:55px">ETF PAIRS</div>
   <div class="subtab" style="left:695px;top:110px;width:155px;height:45px">FACTORS</div>
   <div class="subtab" style="left:855px;top:120px;width:155px;height:35px">NEW TAB TITLE #1</div>
   <div class="subtab" style="left:1015px;top:120px;width:155px;height:35px">NEW TAB TITLE #2</div>
   <div class="subtab" style="left:1175px;top:120px;width:40px;height:35px">
    <svg width="14" height="20" viewBox="0 0 14 20"><path d="M3 2l8 8-8 8" fill="none" stroke="#999" stroke-width="3"/></svg></div>
   <div class="subtab add" style="left:1220px;top:120px;width:40px;height:35px">
    <svg width="24" height="24" viewBox="0 0 24 24"><circle cx="12" cy="12" r="10" fill="none" stroke="#fff" stroke-width="2"/><path d="M12 7v10M7 12h10" stroke="#fff" stroke-width="2"/></svg></div>
  </nav>

  <header class="topbar">
   <div class="brand">KESTREL</div>
   <div class="periods">
    <div class="period active">250D</div>
    <div class="period">83D</div>
    <div class="period">42D</div>
   </div>
   <div class="mainnav">
    <div class="navitem" style="width:141px">
     <svg viewBox="0 0 24 24"><path d="M3 12L12 3l9 9M6 10v11h4v-6h4v6h4V10" fill="none" stroke="#111" stroke-width="2"/></svg>MODELS</div>
    <div class="navitem active" style="width:177px">
     <svg viewBox="0 0 24 24" fill="none" stroke="#fff" stroke-width="1.6"><circle cx="12" cy="12" r="4"/><path d="M12 2v5M12 17v5M2 12h5M17 12h5M5 5l3.5 3.5M15.5 15.5L19 19M19 5l-3.5 3.5M8.5 15.5L5 19"/></svg>SENSITIVITIES</div>
    <div class="navitem" style="width:160px">
     <svg viewBox="0 0 24 24" fill="none" stroke="#111" stroke-width="2"><circle cx="7" cy="7" r="4"/><circle cx="17" cy="7" r="4"/><circle cx="7" cy="17" r="4"/><circle cx="17" cy="17" r="4"/></svg>PORTFOLIO</div>
    <div class="navitem" style="width:152px">
     <svg viewBox="0 0 24 24" fill="none" stroke="#111" stroke-width="2"><rect x="2" y="3" width="20" height="18"/><path d="M5 16l5-5 3 3 6-6"/></svg>BACKTEST</div>
   </div>
  </header>

  <div class="export">
   <svg width="26" height="24" viewBox="0 0 26 24" fill="none" stroke="#02326a" stroke-width="2.4"><path d="M11 5H4v16h16v-7"/><path d="M10 15c1-6 6-9 12-9M17 2l5 4-5 4"/></svg>Export</div>

  <table class="data">
   <thead><tr>
    <th class="factor">Factor</th><th class="id">ID &#8964;</th><th class="sector">Sector</th>
    <th class="stat">Stat 1</th><th class="stat">Stat 2</th><th class="stat">Stat 3</th><th class="stat">Stat 4</th>
    <th class="stat">Stat 5</th><th class="stat">Stat 6</th><th class="stat">Stat 7</th><th class="stat">Stat 8</th>
   </tr></thead>
   <tbody>
    <tr><td>Factor 1</td><td>Model 1</td><td>Materials</td><td>-1.4</td><td>0.1</td><td>-3.1</td><td>0.7</td><td>30.2</td><td>0.9</td><td>-3.1</td><td>0.1</td></tr>
    <tr><td>Factor 2</td><td>Model 2</td><td>Materials</td><td>2.8</td><td>0.1</td><td>6.1</td><td>100</td><td>30.2</td><td>0.9</td><td>6.1</td><td>0.1</td></tr>
    <tr><td>Factor 3</td><td>Model 3</td><td>Materials</td><td>-3.7</td><td>2.7</td><td>-7.2</td><td>100</td><td>30.2</td><td>0.9</td><td>-7.2</td><td>2.7</td></tr>
    <tr><td>Factor 4</td><td>Model 4</td><td>Industrials</td><td>2.8</td><td>0.2</td><td>2.7</td><td>0.5</td><td>32.9</td><td>-0.5</td><td>2.7</td><td>0.2</td></tr>
    <tr><td>Factor 5</td><td>Model 5</td><td>Industrials</td><td>0.8</td><td>0.3</td><td>2.5</td><td>0.5</td><td>32.9</td><td>-0.5</td><td>2.5</td><td>0.3</td></tr>
   </tbody>
  </table>

  <aside class="filters"><span>FILTERS</span></aside>
  <div class="filters-toggle">
   <svg width="22" height="22" viewBox="0 0 22 22"><circle cx="11" cy="11" r="11" fill="#02326a"/><path d="M6 11h9M11 7l4 4-4 4" fill="none" stroke="#fff" stroke-width="2"/></svg>
  </div>
 </div>
</div>
</body>
</html>
```